Accounting firm needing business card / letterhead designed
Marcus L. Trenholm, CPA
marcus@veltrowledger.com
www.veltrowledger.com
842 E Alder Ave Perrysburg, OH 43827
419-562-0974

```html
<!DOCTYPE html>
<html lang="en">
<head>
<meta charset="utf-8">
<title>Veltrow Ledger — Business Card</title>
<link rel="stylesheet" href="https://fonts.googleapis.com/css2?family=Source+Sans+3:wght@400;600&display=swap">
<style>
  :root {
    --backdrop: #878787;
    --navy: #261f63;
    --navy-soft: #2d2670;
    --green: #8cc63f;
    --white: #ffffff;
  }
  * { margin: 0; padding: 0; box-sizing: border-box; }
  html, body { width: 1200px; height: 900px; overflow: hidden; }
  body {
    background: var(--backdrop);
    font-family: "Source Sans 3", sans-serif;
    position: relative;
  }
  .card {
    position: absolute;
    top: 306px;
    width: 439px;
    height: 271px;
    border-radius: 12px;
    overflow: hidden;
  }
  .card-front { left: 149px; background: var(--navy); }
  .card-back { left: 609px; background: var(--navy); }

  .front-header {
    position: absolute; left: 0; top: 0;
    width: 100%; height: 122px;
    background: var(--white);
    border-bottom: 5px solid var(--green);
  }
  .brand-name {
    position: absolute; left: 26px; top: 36px;
    font-weight: 600; font-size: 36px; letter-spacing: 1.5px;
    color: var(--navy); text-transform: uppercase; line-height: 1;
  }
  .holder-name {
    position: absolute; left: 30px; top: 152px;
    font-weight: 600; font-size: 16px; color: var(--green);
    text-transform: uppercase; letter-spacing: 0.2px;
  }
  .contact-list {
    position: absolute; left: 30px; top: 196px;
    list-style: none; color: var(--white); font-size: 12.5px; line-height: 16px;
  }
  .contact-list li { display: flex; align-items: center; gap: 5px; }
  .contact-list svg { width: 10px; height: 10px; fill: var(--green); flex: none; }
  .office-address {
    position: absolute; right: 20px; top: 212px;
    color: var(--white); font-size: 12.5px; line-height: 16px; text-align: right;
    font-style: normal;
  }

  .back-texture {
    position: absolute; inset: 0;
    background: linear-gradient(135deg, var(--navy-soft), var(--navy));
  }
  .back-brand {
    position: absolute; left: 250px; top: 182px; width: 130px;
    text-align: center; color: var(--white);
    font-weight: 600; font-size: 15px; letter-spacing: 1px; text-transform: uppercase;
    white-space: nowrap;
  }
</style>
</head>
<body>
  <section class="card card-front">
    <header class="front-header">
      <div class="brand-name">Veltrow Ledger</div>
    </header>
    <h1 class="holder-name">Marcus L. Trenholm, CPA</h1>
    <ul class="contact-list">
      <li><svg viewBox="0 0 10 10"><path d="M2 0.5 L3.6 2.6 L2.8 3.6 Q4 6 6.4 7.2 L7.4 6.4 L9.5 8 L8.4 9.5 Q4.5 9.5 2 7 Q0.5 5 0.5 1.6 Z"/></svg>419-562-0974</li>
      <li><svg viewBox="0 0 10 10"><path d="M0.5 2 H9.5 V8.5 H0.5 Z M1 2.3 L5 5.6 L9 2.3" stroke="#261f63" stroke-width="0.8"/></svg>marcus@veltrowledger.com</li>
      <li><svg viewBox="0 0 10 10"><circle cx="5" cy="5" r="4.6"/><path d="M0.6 5 H9.4 M5 0.4 V9.6 M5 0.4 Q2 5 5 9.6 M5 0.4 Q8 5 5 9.6" stroke="#261f63" stroke-width="0.7" fill="none"/></svg>www.veltrowledger.com</li>
    </ul>
    <address class="office-address">842 E Alder Ave Perrysburg,<br>OH 43827</address>
  </section>

  <section class="card card-back">
    <div class="back-texture" role="img" aria-label="Repeating faint brand-name pattern across the navy back"></div>
    <div class="back-brand">Veltrow Ledger</div>
  </section>
</body>
</html>
```